I need new business cards designed

I would like to get some new designs on business cards. I will upload my logo for reference. The business cards that were designed for me a few months ago were too difficult for the print companies to work with. My company is Quillbrook.net LLC. It is an art company that sells painting and expression cards online.

```html
<!DOCTYPE html>
<html lang="en">
<head>
<meta charset="utf-8">
<title>Quillbrook.net — Business Cards</title>
<link rel="stylesheet" href="https://fonts.googleapis.com/css2?family=Montserrat:wght@400;500;700&family=Open+Sans:wght@400;600&display=swap">
<style>
  :root {
    --stage: #3a3a3a;
    --navy: #202a6c;
    --ink: #1e1e2a;
    --grey: #6b6e7a;
    --white: #ffffff;
    --blue: #08a2d9;
    --green: #8cc63f;
    --orange: #f39423;
    --red: #e8262a;
  }
  * { margin: 0; padding: 0; box-sizing: border-box; }
  html, body { width: 1200px; height: 1200px; overflow: hidden; }
  body {
    background: var(--stage);
    position: relative;
    font-family: "Montserrat", sans-serif;
  }
  .card {
    position: absolute;
    left: 140px;
    width: 920px;
    height: 526px;
    border-radius: 34px;
    overflow: hidden;
    box-shadow: 0 14px 30px rgba(0,0,0,.35);
  }
  .card--front { top: 44px; background: var(--white); }
  .card--back { top: 630px; background: var(--navy); }

  .stripe {
    position: absolute; left: 0; right: 0; bottom: 0; height: 24px;
    display: flex;
  }
  .stripe span { display: block; height: 100%; }
  .stripe .s-blue { width: 28%; background: var(--blue); }
  .stripe .s-green { width: 24%; background: var(--green); }
  .stripe .s-orange { width: 25%; background: var(--orange); }
  .stripe .s-red { width: 23%; background: var(--red); }

  /* Front: identity */
  .identity {
    position: absolute; left: 70px; top: 224px;
    border-left: 6px solid var(--navy);
    padding-left: 18px;
  }
  .identity__name {
    font-weight: 700; font-size: 44px; color: var(--navy);
    letter-spacing: .5px; line-height: 1;
  }
  .identity__role {
    font-weight: 400; font-size: 17px; color: var(--grey);
    letter-spacing: 1px; margin-top: 4px;
  }
  .contacts {
    position: absolute; left: 96px; top: 320px;
    list-style: none;
  }
  .contacts li {
    display: flex; align-items: flex-start; gap: 14px;
    font-size: 20px; color: var(--ink); line-height: 1.2;
    margin-bottom: 10px;
  }
  .contacts svg { width: 22px; height: 22px; flex: none; margin-top: 1px; }

  /* Brand lockup */
  .brand { position: absolute; display: flex; align-items: center; }
  .brand__square { flex: none; }
  .brand__name {
    font-family: "Open Sans", sans-serif; font-weight: 400; line-height: 1;
  }
  .brand__tagline {
    font-family: "Open Sans", sans-serif; font-weight: 400; white-space: nowrap;
  }
  .card--front .brand { left: 530px; top: 120px; flex-direction: column; align-items: flex-start; }
  .card--front .brand__square { width: 110px; height: 110px; background: var(--orange); margin: 0 0 18px 40px; }
  .card--front .brand__name { font-size: 40px; color: var(--navy); }
  .card--front .brand__tagline { font-size: 17px; color: var(--blue); margin-top: 8px; }

  .card--back .brand { left: 130px; top: 150px; gap: 40px; }
  .card--back .brand__square { width: 170px; height: 170px; background: var(--orange); }
  .card--back .brand__name { font-size: 66px; color: var(--white); }
  .card--back .brand__tagline { font-size: 25px; color: var(--blue); margin-top: 10px; }

  .social {
    position: absolute; left: 530px; top: 440px;
    display: flex; align-items: center; gap: 12px;
    font-size: 17px; color: var(--ink);
  }
  .social__dot { width: 24px; height: 24px; border-radius: 50%; background: var(--navy); }
</style>
</head>
<body>

<section class="card card--front" aria-label="Business card front">
  <div class="identity">
    <h1 class="identity__name">JOHN DOE</h1>
    <p class="identity__role">POSITION</p>
  </div>
  <ul class="contacts">
    <li>
      <svg viewBox="0 0 24 24" aria-hidden="true"><path fill="#202a6c" d="M6.6 10.8a15.1 15.1 0 0 0 6.6 6.6l2.2-2.2a1 1 0 0 1 1-.25 11.4 11.4 0 0 0 3.6.57 1 1 0 0 1 1 1V20a1 1 0 0 1-1 1A17 17 0 0 1 3 4a1 1 0 0 1 1-1h3.5a1 1 0 0 1 1 1c0 1.250.2 2.45.57 3.57a1 1 0 0 1-.25 1z"/></svg>
      (000) 000 0000
    </li>
    <li>
      <svg viewBox="0 0 24 24" aria-hidden="true"><rect x="2" y="5" width="20" height="14" fill="#202a6c"/><path d="M2 5l10 8 10-8" fill="none" stroke="#fff" stroke-width="1.6"/></svg>
      email@company.com
    </li>
    <li>
      <svg viewBox="0 0 24 24" aria-hidden="true"><g fill="none" stroke="#202a6c" stroke-width="1.8"><circle cx="12" cy="12" r="9.5"/><ellipse cx="12" cy="12" rx="4" ry="9.5"/><path d="M2.5 12h19M4 7h16M4 17h16"/></g></svg>
      www.company.com
    </li>
    <li>
      <svg viewBox="0 0 24 24" aria-hidden="true"><path fill="#202a6c" d="M12 2a7 7 0 0 0-7 7c0 5 7 13 7 13s7-8 7-13a7 7 0 0 0-7-7zm0 9.5A2.5 2.5 0 1 1 12 6.5a2.5 2.5 0 0 1 0 5z"/></svg>
      <span>123 Name Street, 000<br>Your City, 00000-000</span>
    </li>
  </ul>

  <div class="brand">
    <div class="brand__square"></div>
    <div>
      <p class="brand__name">Quillbrook.net</p>
      <p class="brand__tagline">Paint Freely · Share Warmly · Create Boldly</p>
    </div>
  </div>

  <div class="social">
    <span class="social__dot"></span>
    <span>@Quillbrook</span>
  </div>

  <div class="stripe"><span class="s-blue"></span><span class="s-green"></span><span class="s-orange"></span><span class="s-red"></span></div>
</section>

<section class="card card--back" aria-label="Business card back">
  <div class="brand">
    <div class="brand__square"></div>
    <div>
      <p class="brand__name">Quillbrook.net</p>
      <p class="brand__tagline">Paint Freely · Share Warmly · Create Boldly</p>
    </div>
  </div>
  <div class="stripe"><span class="s-blue"></span><span class="s-green"></span><span class="s-orange"></span><span class="s-red"></span></div>
</section>

</body>
</html>
```